Book cover design for a collection of poetry - The Lanternfield

Book cover and back design need to be moody, nostalgic, reflective, ethereal. Melancholy and other worldly. Cover design should not be time specific to a period or place but if applicable should reflect British landscape. Book cover should be in tones of blue and must include the title and author (THE LANTERNFIELD BY CORBIN WHITLACE). We love the idea of rain, and looking out of a window. See attached designs. A world you are observing but not in.

Industry/Entity Type

Book Publisher

Font styles to use
Serif
Script

Colors
3176b5
3377b5
85acd3
eaf1f7
0792cd
33a6d7
86cae7
ecf7fb
86cfc6

Requirements
Must have
• The colour blue in it, must be melancholy and reflective.
Nice to have
• Rain in the cover.
Should not have
• Any bright colours.

```html
<!DOCTYPE html>
<html lang="en">
<head>
<meta charset="utf-8">
<title>The Lanternfield — Cover Spread</title>
<link rel="stylesheet" href="https://fonts.googleapis.com/css2?family=Josefin+Sans:wght@400;600;700&display=swap">
<style>
  :root {
    --ink-night: #08131b;
    --ink-deep: #10232e;
    --ink-slate: #1d3a46;
    --sea-dark: #1c3a44;
    --sea-mid: #35606b;
    --sea-teal: #2f5d63;
    --sea-mist: #6f979e;
    --sea-pale: #9dbcc0;
    --paper: #f2f6f8;
  }
  * { margin: 0; padding: 0; box-sizing: border-box; }
  html, body { width: 1200px; height: 864px; overflow: hidden; background: var(--ink-night); }
  .spread { position: relative; width: 1200px; height: 864px; overflow: hidden; color: var(--paper); font-family: "Josefin Sans", sans-serif; }

  .back-cover {
    position: absolute; left: 0; top: 0; width: 573px; height: 864px;
    background:
      radial-gradient(ellipse 70% 45% at 35% 15%, rgba(52, 96, 108, 0.55) 0%, rgba(52, 96, 108, 0) 100%),
      radial-gradient(ellipse 60% 40% at 20% 60%, rgba(34, 70, 80, 0.45) 0%, rgba(34, 70, 80, 0) 100%),
      linear-gradient(180deg, var(--ink-slate) 0%, var(--ink-deep) 45%, var(--ink-night) 100%);
  }
  .spine {
    position: absolute; left: 573px; top: 0; width: 51px; height: 864px;
    background: linear-gradient(180deg, #15303b 0%, var(--ink-deep) 50%, var(--ink-night) 100%);
  }
  .front-cover {
    position: absolute; left: 624px; top: 0; width: 576px; height: 864px;
  }
  .front-scene {
    position: absolute; inset: 0;
    background:
      radial-gradient(ellipse 60% 18% at 45% 30%, rgba(157, 188, 192, 0.55) 0%, rgba(157, 188, 192, 0) 100%),
      radial-gradient(ellipse 45% 20% at 70% 52%, rgba(111, 151, 158, 0.45) 0%, rgba(111, 151, 158, 0) 100%),
      linear-gradient(90deg, rgba(8, 19, 27, 0.45) 0%, rgba(8, 19, 27, 0) 14%),
      linear-gradient(180deg, #3b626c 0%, var(--sea-mist) 22%, #5f8a90 34%, var(--sea-teal) 46%, #4b767c 56%, var(--sea-teal) 70%, var(--sea-dark) 86%, #16303a 100%);
  }

  .divider { position: absolute; display: block; }

  .blurb {
    position: absolute; left: 46px; width: 475px; text-align: center;
    text-transform: uppercase; font-size: 11.5px; line-height: 20px; letter-spacing: 3px;
  }
  .blurb-lead { top: 260px; font-weight: 700; letter-spacing: 3.5px; }
  .blurb-story { top: 306px; }
  .blurb-themes { top: 490px; }

  .spine-title, .spine-author {
    position: absolute; left: 50%; transform: translateX(-50%);
    writing-mode: vertical-rl; font-family: "Josefin Sans", sans-serif; font-weight: 400;
    text-transform: uppercase; white-space: nowrap;
  }
  .spine-title { top: 86px; font-size: 26px; letter-spacing: 1px; }
  .spine-author { top: 533px; font-size: 24px; letter-spacing: 1.5px; }

  .front-title {
    position: absolute; left: 0; width: 576px; top: 446px; text-align: center;
    font-weight: 600; text-transform: uppercase; line-height: 1;
  }
  .front-title span { display: block; }
  .front-title .line-article { font-size: 80px; letter-spacing: 2px; }
  .front-title .line-name { font-size: 66px; letter-spacing: 1px; margin-top: 26px; }
  .front-author {
    position: absolute; left: 0; width: 576px; top: 689px; text-align: center;
    font-size: 25px; font-weight: 700; letter-spacing: 2px;
  }
</style>
</head>
<body>
<main class="spread">

  <section class="back-cover" role="img" aria-label="Dark night photograph of rain drops running down a window pane">
    <svg class="divider" style="left:150px;top:203px" width="267" height="16" viewBox="0 0 267 16" aria-hidden="true">
      <line x1="20" y1="8" x2="124" y2="8" stroke="var(--paper)" stroke-width="1.5"/>
      <circle cx="133" cy="8" r="5" fill="none" stroke="var(--paper)" stroke-width="1.5"/>
      <line x1="142" y1="8" x2="247" y2="8" stroke="var(--paper)" stroke-width="1.5"/>
    </svg>

    <p class="blurb blurb-lead">The Lanternfield is a collection of poetry.</p>
    <p class="blurb blurb-story">Told in two parts we first meet Charles – aged, crippled and left alone in his inherited marsh house – reflecting on his life and his marriage to beautiful Alice who we meet in part two. Alice is suicidal, manically depressed and struggling with life as a wife and mother. She meets, harbors and falls in love with a soldier during WWII and her world is changed forever.</p>
    <p class="blurb blurb-themes">Moving through the 20th century, this life and the next, The Lanternfield interweaves grief, loss, the after-life, mental illness, and ultimately the true nature of love.</p>

    <svg class="divider" style="left:150px;top:609px" width="267" height="16" viewBox="0 0 267 16" aria-hidden="true">
      <line x1="20" y1="8" x2="124" y2="8" stroke="var(--paper)" stroke-width="1.5"/>
      <circle cx="133" cy="8" r="5" fill="none" stroke="var(--paper)" stroke-width="1.5"/>
      <line x1="142" y1="8" x2="247" y2="8" stroke="var(--paper)" stroke-width="1.5"/>
    </svg>
  </section>

  <section class="spine">
    <p class="spine-title">The Lanternfield</p>
    <p class="spine-author">Corbin Whitlace</p>
  </section>

  <section class="front-cover">
    <div class="front-scene" role="img" aria-label="Photograph through a rain-streaked window of a misty blue British moorland with a distant cottage and trees"></div>
    <h1 class="front-title">
      <span class="line-article">The</span>
      <span class="line-name">Lanternfield</span>
    </h1>
    <svg class="divider" style="left:168px;top:655px" width="240" height="16" viewBox="0 0 240 16" aria-hidden="true">
      <line x1="18" y1="8" x2="111" y2="8" stroke="var(--paper)" stroke-width="1.5"/>
      <circle cx="120" cy="8" r="5" fill="none" stroke="var(--paper)" stroke-width="1.5"/>
      <line x1="129" y1="8" x2="222" y2="8" stroke="var(--paper)" stroke-width="1.5"/>
    </svg>
    <p class="front-author">CORBIN WHITLACE</p>
    <svg class="divider" style="left:168px;top:731px" width="240" height="16" viewBox="0 0 240 16" aria-hidden="true">
      <line x1="18" y1="8" x2="111" y2="8" stroke="var(--paper)" stroke-width="1.5"/>
      <circle cx="120" cy="8" r="5" fill="none" stroke="var(--paper)" stroke-width="1.5"/>
      <line x1="129" y1="8" x2="222" y2="8" stroke="var(--paper)" stroke-width="1.5"/>
    </svg>
  </section>

</main>
</body>
</html>
```